Flat Belly Design Graphics for Social

I want to create 9 social media graphics (new Instagram size 4:5 (1080 x 1350 pixels) focusing on our Flat Belly Graphics, using the pics attached. Use the attached pics, NO RANDOM STOCK PHOTOGRAPHY. For the color scheme of the graphics, the color palette is attached. YOU MUST POST ALL 9 GRAPHICS IN ONE ENTRY.
Using the 3 titles below, create one set of graphics. 1) with all text, then for the others, use the pictures as detailed below in IMPORTANT:
1. Ten-Week Bright Morning Reboot
2. The Quick Garden Kitchen Menu Guide
3. Studio Habits for Lasting Energy Past Midlife - Zero Gym Needed
IMPORTANT:
Only use RK Pic 1 and RK Pic 2 with the title, Ten-Week Bright Morning Reboot
Only use meal plan1 and meal plan2 pics with the title, Quick Garden Kitchen Menu Guide
Only use studio habits 1 and studio habits 2 pics with the title, Studio Habits for Lasting Energy Past Midlife - Zero Gym Needed
women over 40

```html
<!DOCTYPE html>
<html lang="en">
<head>
<meta charset="utf-8">
<title>Social Graphics Set</title>
<link rel="stylesheet" href="https://fonts.googleapis.com/css2?family=Oswald:wght@500;700&family=Lato:wght@400;700;900&family=Kaushan+Script&family=Caveat:wght@600&display=swap">
<style>
  :root{
    --board:#4a4a4a;
    --blush:#fde9ee;
    --rose:#e297ae;
    --rose-soft:#f6d2dc;
    --forest:#2c4a47;
    --white:#ffffff;
    --photo-skin:#c9a08a;
    --photo-dark:#3a2f2c;
    --food-a:#e9b7a6;
    --food-b:#a8c48a;
  }
  *{margin:0;padding:0;box-sizing:border-box}
  html,body{width:1200px;height:904px;overflow:hidden;background:var(--board)}
  .board{position:relative;width:1200px;height:904px;background:var(--board)}
  .poster,.tile{position:absolute;overflow:hidden;background:var(--blush)}
  .poster{left:35px;top:30px;width:442px;height:556px}
  .tile{width:218px;height:272px}
  .c1{left:490px}.c2{left:723px}.c3{left:954px}
  .r1{top:29px}.r2{top:315px}.r3{top:599px}
  .abs{position:absolute;white-space:nowrap}
  .cond{font-family:"Oswald",sans-serif;font-weight:700;text-transform:uppercase;line-height:.95}
  .sans{font-family:"Lato",sans-serif;font-weight:900;text-transform:uppercase;line-height:1}
  .script{font-family:"Kaushan Script",cursive;line-height:1}
  .hand{font-family:"Caveat",cursive;line-height:1}
  .rose{color:var(--rose)}.forest{color:var(--forest)}.white{color:var(--white)}
  .photo-person{background:linear-gradient(180deg,var(--photo-dark) 0%,var(--photo-skin) 35%,#f2ece8 60%,var(--photo-dark) 100%)}
  .photo-pair{background:linear-gradient(160deg,#efe3dc 0%,var(--photo-skin) 45%,#6b4a3e 100%)}
  .photo-food{background:linear-gradient(90deg,var(--food-a),var(--food-b),#d9a46a,var(--food-a))}
  .badge{border-radius:50%;display:flex;align-items:center;justify-content:center;text-align:center}
  .rule{height:1px;background:var(--forest)}
</style>
</head>
<body>
<div class="board">

  <!-- Hero poster -->
  <section class="poster">
    <div class="abs photo-person" role="img" aria-label="Smiling woman in white cropped sweater pointing at her waist" style="left:0;top:75px;width:240px;height:481px;opacity:.85"></div>
    <div class="abs" style="left:247px;top:0;width:171px;height:158px;background:var(--rose)"></div>
    <div class="abs cond white" style="left:252px;top:22px;width:162px;font-size:60px;text-align:center">Ten<br>Week</div>
    <div class="abs cond forest" style="left:246px;top:172px;width:172px;font-size:66px;text-align:right">Bright</div>
    <div class="abs cond forest" style="left:246px;top:240px;width:172px;font-size:40px;text-align:right">Morning</div>
    <div class="abs badge" style="left:283px;top:390px;width:136px;height:136px;background:var(--white)">
      <span class="script rose" style="font-size:30px">Reboot</span>
    </div>
  </section>

  <!-- Menu guide, food frame -->
  <section class="tile c1 r1">
    <div class="abs photo-food" role="img" aria-label="Overhead spread of chicken, berries, grains and vegetables" style="left:0;top:0;width:218px;height:52px"></div>
    <div class="abs photo-food" role="img" aria-label="Bowls of nuts and grains along the edge" style="left:196px;top:60px;width:22px;height:140px"></div>
    <div class="abs photo-food" role="img" aria-label="Chickpeas and asparagus on the left edge" style="left:0;top:70px;width:14px;height:120px"></div>
    <div class="abs sans forest" style="left:40px;top:68px;font-size:13px">The</div>
    <div class="abs cond rose" style="left:40px;top:84px;font-size:46px">Quick</div>
    <div class="abs cond rose" style="left:40px;top:132px;font-size:38px">Garden</div>
    <div class="abs sans forest" style="left:40px;top:200px;font-size:18px;font-weight:700;line-height:1.1">Kitchen Menu<br>Guide</div>
  </section>

  <!-- Studio habits, text top -->
  <section class="tile c2 r1">
    <div class="cond rose abs" style="left:0;top:10px;width:218px;text-align:center;font-size:34px;font-weight:500">Studio<br>Habits</div>
    <div class="abs rule" style="left:22px;top:90px;width:174px"></div>
    <div class="abs" style="left:22px;top:95px;width:174px;text-align:center;line-height:18px">
      <span class="cond forest" style="font-size:14px">Lasting Energy</span>
      <span class="script forest" style="font-size:12px">Past Midlife</span>
    </div>
    <div class="abs rule" style="left:22px;top:117px;width:174px"></div>
    <div class="abs sans forest" style="left:0;top:124px;width:218px;text-align:center;font-size:9px;font-weight:400">Zero Gym Needed</div>
    <div class="abs photo-pair" role="img" aria-label="Two women sharing a whisper, one surprised" style="left:0;top:142px;width:218px;height:130px"></div>
  </section>

  <!-- Ten-week, photo right -->
  <section class="tile c3 r1">
    <div class="abs photo-person" role="img" aria-label="Smiling woman in white cropped sweater" style="left:120px;top:0;width:98px;height:272px;opacity:.85"></div>
    <div class="abs cond rose" style="left:10px;top:40px;font-size:42px">Ten<br>Week</div>
    <div class="abs cond forest" style="left:10px;top:140px;font-size:22px">Bright<br>Morning</div>
    <div class="abs" style="left:14px;top:214px;width:86px;height:28px;border-radius:14px;background:var(--forest);display:flex;align-items:center;justify-content:center">
      <span class="script rose" style="font-size:15px">Reboot</span>
    </div>
  </section>

  <!-- Studio habits, photo right -->
  <section class="tile c1 r2">
    <div class="abs" style="left:150px;top:-40px;width:160px;height:160px;border-radius:50%;background:var(--rose-soft)"></div>
    <div class="abs" style="left:-60px;top:190px;width:170px;height:170px;border-radius:50%;background:var(--rose-soft)"></div>
    <div class="abs photo-pair" role="img" aria-label="Two women, one whispering to the other who looks excited" style="left:104px;top:70px;width:114px;height:202px"></div>
    <div class="abs sans rose" style="left:14px;top:12px;font-size:23px">Studio<br>Habits</div>
    <div class="abs sans forest" style="left:14px;top:80px;font-size:11px;font-weight:400">For</div>
    <div class="abs cond forest" style="left:14px;top:94px;font-size:21px">Lasting<br>Energy</div>
    <div class="abs badge" style="left:14px;top:156px;width:66px;height:66px;background:var(--white)">
      <span class="script forest" style="font-size:12px;white-space:normal">Past<br>Midlife</span>
    </div>
    <div class="abs sans forest" style="left:7px;top:236px;width:80px;text-align:center;font-size:9px;font-weight:400">Zero Gym<br>Needed</div>
  </section>

  <!-- Ten-week, vertical headline -->
  <section class="tile c2 r2">
    <div class="abs photo-person" role="img" aria-label="Smiling woman in white cropped sweater pointing at her waist" style="left:96px;top:60px;width:122px;height:212px;opacity:.85"></div>
    <div class="abs cond rose" style="left:-90px;top:108px;width:260px;height:56px;font-size:54px;transform:rotate(-90deg);text-align:center;line-height:56px">Ten-Week</div>
    <div class="abs cond forest" style="left:100px;top:20px;font-size:15px;font-weight:500">Bright Morning</div>
    <div class="abs sans rose" style="left:100px;top:40px;font-size:14px;font-weight:700">Reboot</div>
  </section>

  <!-- Menu guide, notebook -->
  <section class="tile c3 r2">
    <div class="abs photo-food" role="img" aria-label="Fresh produce, salmon, avocado and tomatoes around the frame" style="left:0;top:0;width:218px;height:272px"></div>
    <div class="abs" style="left:30px;top:40px;width:165px;height:208px;background:var(--white);border-radius:6px;transform:rotate(-4deg)"></div>
    <div class="abs badge" style="left:82px;top:58px;width:72px;height:72px;background:var(--rose)">
      <span class="cond white" style="font-size:20px">Quick</span>
    </div>
    <div class="abs cond forest" style="left:50px;top:128px;font-size:15px;transform:rotate(-4deg)">The</div>
    <div class="abs cond forest" style="left:58px;top:138px;font-size:32px;transform:rotate(-4deg)">Garden</div>
    <div class="abs sans rose" style="left:62px;top:178px;font-size:14px;transform:rotate(-4deg)">Kitchen</div>
    <div class="abs hand forest" style="left:66px;top:198px;font-size:22px;transform:rotate(-4deg)">Menu Guide</div>
  </section>

  <!-- Ten-week, dark outfit -->
  <section class="tile c1 r3">
    <div class="abs photo-person" role="img" aria-label="Woman in sheer black top and black jeans" style="left:112px;top:0;width:106px;height:272px;opacity:.8"></div>
    <div class="abs cond forest" style="left:10px;top:16px;font-size:40px">Ten<br>Week</div>
    <div class="abs cond rose" style="left:12px;top:100px;font-size:28px">Bright</div>
    <div class="abs sans rose" style="left:12px;top:136px;font-size:16px;font-weight:700">Morning</div>
    <div class="abs badge" style="left:14px;top:204px;width:54px;height:54px;background:var(--forest)">
      <span class="script rose" style="font-size:11px">Reboot</span>
    </div>
  </section>

  <!-- Menu guide, framed -->
  <section class="tile c2 r3">
    <div class="abs photo-food" role="img" aria-label="Overhead food spread of asparagus, berries and grains" style="left:0;top:0;width:218px;height:22px"></div>
    <div class="abs photo-food" role="img" aria-label="Overhead food spread of berries, chicken and cheese" style="left:0;top:216px;width:218px;height:56px"></div>
    <div class="abs" style="left:42px;top:32px;width:134px;height:176px;border:1px solid var(--forest)"></div>
    <div class="abs sans forest" style="left:92px;top:25px;padding:0 5px;background:var(--blush);font-size:13px">The</div>
    <div class="abs cond rose" style="left:42px;top:54px;width:134px;text-align:center;font-size:46px">Quick</div>
    <div class="abs cond rose" style="left:42px;top:104px;width:134px;text-align:center;font-size:30px">Garden</div>
    <div class="abs sans forest" style="left:38px;top:166px;width:142px;padding:2px 0;background:var(--blush);text-align:center;font-size:14px;font-weight:700;line-height:1.1">Kitchen Menu<br>Guide</div>
  </section>

  <!-- Studio habits, photo top -->
  <section class="tile c3 r3">
    <div class="abs photo-pair" role="img" aria-label="Two women sharing a whispered secret" style="left:-20px;top:-110px;width:258px;height:258px;border-radius:50%"></div>
    <div class="abs cond forest" style="left:0;top:156px;width:218px;text-align:center;font-size:22px;font-weight:500">Studio Habits</div>
    <div class="abs sans forest" style="left:0;top:184px;width:218px;text-align:center;font-size:9px;font-weight:400">For</div>
    <div class="abs cond rose" style="left:0;top:196px;width:218px;text-align:center;font-size:24px;font-weight:500">Lasting Energy</div>
    <div class="abs script forest" style="left:0;top:224px;width:218px;text-align:center;font-size:15px">Past Midlife</div>
    <div class="abs sans forest" style="left:0;top:254px;width:218px;text-align:center;font-size:8px;font-weight:400">Zero Gym Needed</div>
  </section>

</div>
</body>
</html>
```